Local Roofing/Construction company business needs new biz card design

We need a new business card design, current cards are from the start of this operation and generic at best. We are a local Construction Company (General Contractor) with a majority of our work originating from insurance claims-exterior finish work is the main focus (Roofs-Siding-Gutters etc). Heavily involved with homeowners and the low ball offers they receive from insurance company's after a insurable event takes place. I have attached some of our original logo file(s) below.

```html
<!DOCTYPE html>
<html lang="en">
<head>
<meta charset="utf-8">
<title>Halvard Build Co – Business Card</title>
<link rel="stylesheet" href="https://fonts.googleapis.com/css2?family=Poppins:wght@300;400;600;700&display=swap">
<style>
  :root {
    --backdrop: #2b2b2d;
    --card: #1c1d1f;
    --green: #2fd576;
    --white: #f4f2ef;
    --grey: #c9c9c9;
    --rule: #55575a;
  }
  * { margin: 0; padding: 0; box-sizing: border-box; }
  html, body { width: 1200px; height: 1108px; overflow: hidden; }
  body {
    background: var(--backdrop);
    font-family: "Poppins", sans-serif;
    position: relative;
  }
  .card {
    position: absolute;
    top: 224px;
    width: 420px;
    height: 660px;
    border-radius: 18px;
    overflow: hidden;
    background: var(--card);
  }
  .card-front { left: 150px; }
  .card-back { left: 630px; }

  .front-inner {
    height: 100%;
    display: flex;
    flex-direction: column;
    align-items: center;
    padding-top: 96px;
    text-align: center;
  }
  .brand {
    display: flex;
    flex-direction: column;
    align-items: center;
    gap: 18px;
  }
  .brand-square {
    width: 64px;
    height: 64px;
    background: var(--green);
    border-radius: 8px;
  }
  .brand-name {
    color: var(--green);
    font-weight: 700;
    font-size: 30px;
    line-height: 1.1;
    letter-spacing: 1px;
    text-transform: uppercase;
  }
  .person { margin-top: 68px; }
  .person-name {
    color: var(--green);
    font-weight: 700;
    font-size: 27px;
    letter-spacing: 0.5px;
    text-transform: uppercase;
  }
  .person-title {
    color: var(--grey);
    font-weight: 400;
    font-size: 15px;
    letter-spacing: 1px;
    text-transform: uppercase;
    margin-top: -2px;
  }
  .icon-row {
    display: flex;
    align-items: center;
    gap: 10px;
    margin-top: 22px;
    width: 280px;
  }
  .icon-row .rule { flex: 1; height: 1px; background: var(--rule); }
  .icon {
    width: 26px;
    height: 26px;
    background: var(--green);
    border-radius: 4px;
    display: flex;
    align-items: center;
    justify-content: center;
  }
  .contact {
    margin-top: 12px;
    color: var(--white);
    font-size: 17px;
    font-weight: 400;
    line-height: 1.45;
  }
  .divider {
    width: 280px;
    height: 1px;
    background: var(--rule);
    margin: 18px 0 16px;
  }
  .address {
    color: var(--white);
    font-size: 16px;
    line-height: 1.45;
  }

  .back-texture {
    position: absolute;
    inset: 0;
    background: linear-gradient(200deg, #4a4b4d 0%, #2a2b2d 40%, #141516 75%, #0d0d0e 100%);
  }
  .back-name {
    position: absolute;
    right: 52px;
    bottom: 210px;
    color: var(--green);
    font-weight: 700;
    font-size: 20px;
    letter-spacing: 1px;
    text-transform: uppercase;
  }
</style>
</head>
<body>
  <section class="card card-front">
    <div class="front-inner">
      <div class="brand">
        <div class="brand-square"></div>
        <div class="brand-name">Halvard<br>Build Co</div>
      </div>
      <div class="person">
        <div class="person-name">Marcus Hale</div>
        <div class="person-title">Managing Director</div>
      </div>
      <div class="icon-row">
        <span class="rule"></span>
        <span class="icon">
          <svg width="16" height="16" viewBox="0 0 24 24" aria-label="Phone"><path fill="#1c1d1f" d="M6.6 10.8a15 15 0 0 0 6.6 6.6l2.2-2.2c.3-.3.7-.4 1-.2 1.1.4 2.3.6 3.6.6.6 0 1 .4 1 1V20c0 .6-.4 1-1 1A17 17 0 0 1 3 4c0-.6.4-1 1-1h3.5c.6 0 1 .4 1 1 0 1.3.2 2.5.6 3.6.1.3 0 .7-.2 1z"/></svg>
        </span>
        <span class="icon">
          <svg width="16" height="16" viewBox="0 0 24 24" aria-label="Email"><rect x="3" y="6" width="18" height="12" fill="none" stroke="#1c1d1f" stroke-width="2"/><path d="M3 6l9 7 9-7" fill="none" stroke="#1c1d1f" stroke-width="2"/></svg>
        </span>
        <span class="icon">
          <svg width="16" height="16" viewBox="0 0 24 24" aria-label="Website"><circle cx="12" cy="12" r="9" fill="none" stroke="#1c1d1f" stroke-width="2"/><path d="M3 12h18M12 3c3 3 3 15 0 18M12 3c-3 3-3 15 0 18" fill="none" stroke="#1c1d1f" stroke-width="1.6"/></svg>
        </span>
        <span class="rule"></span>
      </div>
      <div class="contact">
        <div>055-310 742 186</div>
        <div>hello@halvardbuild.com</div>
        <div>www.halvardbuild.com</div>
      </div>
      <div class="divider"></div>
      <div class="address">
        <div>18 Ridgeway Lane, Northfield</div>
        <div>60714, Westmark County</div>
      </div>
    </div>
  </section>

  <section class="card card-back">
    <div class="back-texture" role="img" aria-label="Repeating tone-on-tone brand pattern in glossy black and grey"></div>
    <div class="back-name">Halvard Build Co</div>
  </section>
</body>
</html>
```